Redesign of business card for Cedar Ridge Mechanical

We are looking for a new design for our business cards for Cedar Ridge Mechanical. We are a plumbing & HVAC construction company, operating on the West Coast of Canada and USA. Logo attached.
Industry/Entity Type
Construction - Plumbing & HVAC
Contact Information for Business Card
Name, address, phone numbers, email, website address
Look and feel
Each slider illustrates characteristics of the customer's brand and the style your logo design should communicate.

```html
<!DOCTYPE html>
<html lang="en">
<head>
<meta charset="UTF-8">
<title>Cedar Ridge Mechanical — Business Card</title>
<link href="https://fonts.googleapis.com/css2?family=Montserrat:wght@400;500;700&display=swap" rel="stylesheet">
<style>
  :root {
    --backdrop: #222222;
    --card: #121212;
    --ink: #ffffff;
    --ink-soft: #e6e6e6;
  }
  * { margin: 0; padding: 0; box-sizing: border-box; }
  html, body {
    width: 1200px; height: 711px; overflow: hidden;
    background: var(--backdrop);
    font-family: "Montserrat", sans-serif;
    color: var(--ink);
  }
  .stage {
    position: relative; width: 1200px; height: 711px;
    display: flex; justify-content: center; align-items: center; gap: 80px;
  }
  .card {
    width: 300px; height: 510px;
    background: var(--card);
    border-radius: 26px;
    position: relative;
    display: flex; flex-direction: column; align-items: center;
  }
  /* Front */
  .card-front { justify-content: center; }
  .brand-front {
    display: flex; flex-direction: column; align-items: center; gap: 22px;
  }
  .brand-mark {
    width: 64px; height: 64px; border: 6px solid var(--ink); border-radius: 10px;
  }
  .brand-name-front {
    font-weight: 700; font-size: 22px; letter-spacing: 2px;
    text-transform: uppercase; text-align: center; line-height: 1.35;
  }
  /* Back */
  .card-back { padding-top: 54px; }
  .brand-back {
    display: flex; align-items: center; gap: 14px;
  }
  .brand-back .brand-mark { width: 42px; height: 42px; border-width: 5px; border-radius: 8px; }
  .brand-name-back {
    font-weight: 700; font-size: 15px; letter-spacing: 1.5px;
    text-transform: uppercase; line-height: 1.35;
  }
  .person { margin-top: 74px; text-align: center; }
  .person-name { font-weight: 700; font-size: 17px; letter-spacing: 1px; text-transform: uppercase; }
  .person-role { font-weight: 400; font-size: 13px; color: var(--ink-soft); margin-top: 3px; }
  .icon-row {
    margin-top: 18px; width: 230px;
    display: flex; align-items: center; gap: 8px;
  }
  .rule { flex: 1; height: 1.5px; background: var(--ink); }
  .icon {
    width: 24px; height: 24px; border-radius: 6px; background: var(--ink);
    display: flex; align-items: center; justify-content: center;
  }
  .contact-list {
    margin-top: 16px; list-style: none; text-align: center;
    font-size: 13px; line-height: 1.6; color: var(--ink-soft);
  }
  .divider { margin-top: 14px; width: 230px; height: 1.5px; background: var(--ink); }
  .address {
    margin-top: 14px; text-align: center; font-style: normal;
    font-size: 13px; line-height: 1.6; color: var(--ink-soft);
  }
</style>
</head>
<body>
<main class="stage">
  <section class="card card-front" aria-label="Card front">
    <div class="brand-front">
      <span class="brand-mark"></span>
      <p class="brand-name-front">Cedar Ridge<br>Mechanical</p>
    </div>
  </section>

  <section class="card card-back" aria-label="Card back">
    <div class="brand-back">
      <span class="brand-mark"></span>
      <p class="brand-name-back">Cedar Ridge<br>Mechanical</p>
    </div>

    <div class="person">
      <p class="person-name">Daniel Reyes</p>
      <p class="person-role">Managing Director</p>
    </div>

    <div class="icon-row">
      <span class="rule"></span>
      <span class="icon" aria-label="Phone">
        <svg width="14" height="14" viewBox="0 0 24 24"><path fill="#121212" d="M6.6 10.8a15 15 0 0 0 6.6 6.6l2.2-2.2a1 1 0 0 1 1-.25 11.4 11.4 0 0 0 3.6.57 1 1 0 0 1 1 1V20a1 1 0 0 1-1 1A17 17 0 0 1 3 4a1 1 0 0 1 1-1h3.5a1 1 0 0 1 1 1c0 1.25.2 2.45.57 3.57a1 1 0 0 1-.25 1z"/></svg>
      </span>
      <span class="icon" aria-label="Email">
        <svg width="14" height="14" viewBox="0 0 24 24"><rect x="2" y="5" width="20" height="14" rx="2" fill="#121212"/><path d="M3 6l9 7 9-7" fill="none" stroke="#fff" stroke-width="1.8"/></svg>
      </span>
      <span class="icon" aria-label="Website">
        <svg width="14" height="14" viewBox="0 0 24 24"><circle cx="12" cy="12" r="10" fill="#121212"/><path d="M2 12h20M12 2c3 3 3 17 0 20M12 2c-3 3-3 17 0 20" fill="none" stroke="#fff" stroke-width="1.4"/></svg>
      </span>
      <span class="rule"></span>
    </div>

    <ul class="contact-list">
      <li>123 456 789</li>
      <li>info@yourgmail.com</li>
      <li>www.yourwebsite.com</li>
    </ul>

    <span class="divider"></span>

    <address class="address">Your address,<br>City State, Zip 1234</address>
  </section>
</main>
</body>
</html>
```